Hueverberant (Synth Presets Expansion Pack)

Hello Designers! I'm an audio engineer and beat maker who is about to start selling sound packs on my website www.brindlemoorstudio.com. I'm looking to have some art created for my new QUARTZEN Preset Bank called "Hueverberant". QUARTZEN is a Synth from Pellow Acoustics if you want to learn more about it. Hueverberant is a sub type of synthesthesia, a syndrome where people see colors when they hear sounds. Check out this video to learn more https://www.vidlorn.com/watch?v=kq7TzwPmd3X
I've attached some examples of another producers sound pack graphics and boxes, so you have an idea of what I'm looking for. I also have attached two pictures of "Hueverberant" to inspire the graphics I'm hoping for on my new product. I would like my product to say "www.BrindleMoorStudio.com Presents" at the top. At the bottom I would like my logo to go on the bottom left. Please also add the Lumo and KT logo on the bottom right. If you have any questions please let me know.

Target Market(s)

97% of my customers are upcoming producers, 18-45 years old, and are guys.

Industry/Entity Type

Audio

Requirements
Must have
• What I asked for in the description.

```html
<!DOCTYPE html>
<html lang="en">
<head>
<meta charset="UTF-8">
<title>Hueverberant – Preset Bank Cover</title>
<link href="https://fonts.googleapis.com/css2?family=Exo+2:wght@600;800&display=swap" rel="stylesheet">
<style>
  :root {
    --backdrop: #a4a5a9;
    --panel: #f2f2f4;
    --navy: #1f2a5c;
    --orange: #f06a1c;
    --magenta: #d02f8e;
    --red: #e4312b;
    --peach: #f7b48a;
    --ink: #1b1b1f;
    --skyline: #c9c9cd;
  }
  * { margin: 0; padding: 0; box-sizing: border-box; }
  html, body { width: 1200px; height: 900px; overflow: hidden; }
  body {
    background: var(--backdrop);
    font-family: "Exo 2", sans-serif;
    position: relative;
  }
  .cover {
    position: absolute;
    left: 320px; top: 50px;
    width: 560px; height: 800px;
    background: var(--panel);
    overflow: hidden;
    box-shadow: 0 20px 40px rgba(0,0,0,0.25);
  }
  .cover__bands { position: absolute; inset: 0; }
  .cover__header {
    position: absolute; top: 22px; left: 0; right: 0;
    text-align: center;
  }
  .cover__url {
    font-weight: 800; font-size: 17px; letter-spacing: 2px;
    color: var(--navy);
  }
  .cover__presents {
    margin-top: 6px;
    font-weight: 800; font-size: 15px; letter-spacing: 9px;
    color: var(--orange);
  }
  .cover__artwork {
    position: absolute; left: 110px; top: 140px;
    width: 340px; height: 460px;
    border-radius: 46% 46% 40% 40%;
    background: radial-gradient(ellipse at 50% 45%, #2a2a30 0%, #55555e 45%, rgba(210,90,150,0.55) 75%, rgba(242,242,244,0) 100%);
  }
  .cover__skyline {
    position: absolute; left: 0; right: 0; bottom: 0; height: 190px;
    background: linear-gradient(to top, var(--skyline) 0%, rgba(201,201,205,0.6) 60%, rgba(242,242,244,0) 100%);
  }
  .cover__brand {
    position: absolute; left: 40px; bottom: 40px;
    display: flex; align-items: center; gap: 10px;
    font-weight: 800; font-size: 26px; color: var(--ink);
  }
  .cover__brand-mark {
    width: 22px; height: 22px; background: var(--ink);
  }
  .cover__platforms {
    position: absolute; right: 34px; bottom: 190px;
    display: flex; gap: 10px;
    font-weight: 800; font-size: 14px; color: var(--magenta);
  }
</style>
</head>
<body>
  <main class="cover">
    <svg class="cover__bands" width="560" height="800" viewBox="0 0 560 800" aria-hidden="true">
      <defs>
        <linearGradient id="band-warm" x1="0" y1="0" x2="1" y2="1">
          <stop offset="0" stop-color="#d02f8e"/>
          <stop offset="0.5" stop-color="#e4312b"/>
          <stop offset="1" stop-color="#f7b48a"/>
        </linearGradient>
      </defs>
      <!-- left diagonal bands -->
      <polygon points="0,40 40,40 190,640 150,640" fill="url(#band-warm)" opacity="0.85"/>
      <polygon points="50,30 62,30 212,630 200,630" fill="var(--navy)"/>
      <polygon points="0,140 14,140 140,660 126,660" fill="var(--ink)"/>
      <polygon points="74,60 96,60 240,600 218,600" fill="#b8bdd6" opacity="0.8"/>
      <!-- right diagonal bands -->
      <polygon points="560,70 530,70 360,560 390,560" fill="url(#band-warm)" opacity="0.85"/>
      <polygon points="500,60 512,60 330,620 318,620" fill="var(--navy)"/>
      <polygon points="560,200 548,200 420,580 432,580" fill="var(--ink)"/>
      <polygon points="470,90 490,90 340,520 320,520" fill="#b8bdd6" opacity="0.8"/>
      <!-- lower sweep -->
      <polygon points="140,760 170,760 440,380 410,380" fill="url(#band-warm)" opacity="0.7"/>
      <polygon points="120,790 130,790 400,410 390,410" fill="var(--ink)"/>
    </svg>

    <header class="cover__header">
      <p class="cover__url">WWW.BRINDLEMOORSTUDIO.COM</p>
      <p class="cover__presents">PRESENTS</p>
    </header>

    <div class="cover__artwork" role="img" aria-label="Illustration of a DJ in headphones with speakers, stars and paint splashes"></div>

    <div class="cover__skyline" role="img" aria-label="Grey city skyline silhouette"></div>

    <div class="cover__platforms">
      <span>KT</span>
      <span>Lumo</span>
    </div>

    <div class="cover__brand">
      <span class="cover__brand-mark"></span>
      <span>BrindleMoor Studio</span>
    </div>
  </main>
</body>
</html>
```